Veltrano.co - Polar Expeditions Specialists

We need a modern, visually striking business card for Veltrano.co, a company specialized in selling expedition cruises to the most remote regions on Earth, with a focus on the Arctic and Antarctica. The design should instantly communicate that the cardholder is an expert in polar travel. Use clean, premium aesthetics with cool tones like icy blue and white, possibly incorporating polar imagery (ice, glaciers, penguins, etc.)

Attached the logo

Contact Information for Business Card

Feels high-end and trustworthy.. Visually memorable — encourages people to keep it

Colors
0054AA
0677BA
7BADD7
CADEEF
E8F1F8

Requirements
Must have
• ice, glaciers, penguins, montains
Nice to have
• modern, transparente,

```html
<!DOCTYPE html>
<html lang="en">
<head>
<meta charset="utf-8">
<title>Veltrano.co Business Card</title>
<link href="https://fonts.googleapis.com/css2?family=Poppins:wght@300;400;500;600;700&display=swap" rel="stylesheet">
<style>
  :root {
    --brand-blue: #2d78ba;
    --ink: #1b1b2b;
    --band-edge: #1a1a33;
    --card-bg: #ffffff;
    --page-bg: #e4e8ea;
  }
  * { margin: 0; padding: 0; box-sizing: border-box; }
  html, body { width: 1200px; height: 960px; overflow: hidden; }
  body {
    background: var(--page-bg);
    font-family: "Poppins", sans-serif;
    position: relative;
  }
  .card {
    position: absolute;
    left: 250px;
    width: 701px;
    height: 400px;
    background: var(--card-bg);
    border-radius: 28px;
    overflow: hidden;
  }
  .card--front { top: 60px; }
  .card--back { top: 500px; }
  .card__band {
    position: absolute;
    left: 0; right: 0; bottom: 0;
    height: 24px;
    background: var(--brand-blue);
    border-top: 2px solid var(--band-edge);
  }
  .brand { position: absolute; text-align: center; color: var(--brand-blue); }
  .brand__dot {
    display: block;
    margin: 0 auto;
    border-radius: 50%;
    background: var(--brand-blue);
  }
  .brand__name { font-weight: 700; line-height: 1; letter-spacing: -0.5px; }
  .brand__tagline { font-weight: 600; line-height: 1; }

  .card--front .brand { left: 0; right: 0; top: 80px; }
  .card--front .brand__dot { width: 104px; height: 104px; margin-bottom: 44px; }
  .card--front .brand__name { font-size: 76px; }
  .card--front .brand__tagline { font-size: 22px; margin-top: 18px; }

  .card--back .brand { left: 42px; width: 260px; top: 126px; }
  .card--back .brand__dot { width: 66px; height: 66px; margin-bottom: 28px; }
  .card--back .brand__name { font-size: 47px; }
  .card--back .brand__tagline { font-size: 13.5px; margin-top: 6px; }

  .contact-frame { position: absolute; left: 0; top: 0; }
  .person { position: absolute; left: 408px; top: 86px; }
  .person__name { font-size: 38px; line-height: 1; color: var(--brand-blue); }
  .person__first { font-weight: 600; }
  .person__last { font-weight: 300; }
  .person__role { font-size: 18px; font-weight: 500; color: var(--ink); margin-top: 4px; }
  .address {
    position: absolute; left: 410px; top: 170px;
    font-size: 18px; line-height: 26px; color: var(--ink); font-style: normal;
  }
  .contacts { position: absolute; left: 408px; top: 238px; list-style: none; }
  .contacts li {
    display: flex; align-items: center; gap: 10px;
    font-size: 19px; line-height: 26px; color: var(--ink);
  }
  .contacts svg { width: 18px; height: 18px; flex: none; }
</style>
</head>
<body>

<section class="card card--front">
  <div class="brand">
    <span class="brand__dot"></span>
    <div class="brand__name">Veltrano.co</div>
    <div class="brand__tagline">Polar Expeditions Specialists</div>
  </div>
  <div class="card__band"></div>
</section>

<section class="card card--back">
  <div class="brand">
    <span class="brand__dot"></span>
    <div class="brand__name">Veltrano.co</div>
    <div class="brand__tagline">Polar Expeditions Specialists</div>
  </div>

  <svg class="contact-frame" width="701" height="400" viewBox="0 0 701 400">
    <g fill="none" stroke="var(--brand-blue)" stroke-width="2">
      <path d="M470 66 H358 Q350 66 350 74 V327 Q350 335 358 335 H470"/>
      <path d="M350 198 H388"/>
    </g>
    <g fill="var(--brand-blue)">
      <circle cx="470" cy="66" r="4.5"/>
      <circle cx="388" cy="198" r="4.5"/>
      <circle cx="470" cy="335" r="4.5"/>
    </g>
  </svg>

  <div class="person">
    <div class="person__name"><span class="person__first">Marta</span> <span class="person__last">Kovalen</span></div>
    <div class="person__role">Founder &amp; CEO</div>
  </div>

  <address class="address">1840 Lakeside Ave. Suite<br>300 Denton, TX 76201</address>

  <ul class="contacts">
    <li>
      <svg viewBox="0 0 24 24"><path fill="var(--brand-blue)" d="M6.6 10.8a15 15 0 0 0 6.6 6.6l2.2-2.2c.3-.3.7-.4 1-.2 1.1.4 2.3.6 3.6.6.6 0 1 .4 1 1V20c0 .6-.4 1-1 1A17 17 0 0 1 3 4c0-.6.4-1 1-1h3.5c.6 0 1 .4 1 1 0 1.3.2 2.5.6 3.6.1.3 0 .7-.2 1z"/></svg>
      (555) 214-3806
    </li>
    <li>
      <svg viewBox="0 0 24 24"><circle cx="12" cy="12" r="9" fill="none" stroke="var(--brand-blue)" stroke-width="2"/><path d="M3 12h18M12 3c3 3 3 15 0 18M12 3c-3 3-3 15 0 18" fill="none" stroke="var(--brand-blue)" stroke-width="1.5"/></svg>
      www.veltranotravel.com
    </li>
    <li>
      <svg viewBox="0 0 24 24"><rect x="2" y="6" width="20" height="14" rx="1.5" fill="none" stroke="var(--brand-blue)" stroke-width="2"/><path d="M2 7l10 7 10-7" fill="none" stroke="var(--brand-blue)" stroke-width="2"/></svg>
      info@veltranotravel.com
    </li>
  </ul>

  <div class="card__band"></div>
</section>

</body>
</html>
```